Real Estate Company Looking for Business Card Designs for 3 Executives

Hello!
Thanks so much for considering our project! We are a real estate investment company located in Edmonton, Alberta called Bellhaven Group of Companies. We invest/develop both commercial and residential real estate and are looking to create 3 DOUBLE-SIDED business cards for 3 top executives in the company! (for some reason it won't let us select the double-sided option, but yes, the cards are double sided and would be happy to tip extra)

We have certain guidelines that we want our business cards to for sure follow - the back of the Business card has to be the Black Background Version of the Logo which has already been designed and linked as a file (first file). We want the entire back of the card to simply just be the black background logo. In terms of the front of the card, would like to see a smaller version of the white background logo (linked as the second file) in the top left hand corner - of course, feel free to get creative and we can make revisions together along the way! and Then after that, just text. We want the card to be sharp, clean, easy on the eyes and highly professional looking. We would like the card to include the Full name of the Company (Bellhaven Group of Companies), Name of the Person, Title, Phone, Email. If possible please provide the front part of the card for 3 people:

1) Bellhaven Group of Companies, Liora Quenby, Chief Financial Officer, 780-555-0142, lioraquenby@bellhavengroup.example

2) Bellhaven Group of Companies, Tobias Quenby, Chief Executive Officer, 780-555-0187, tobiasquenby@bellhavengroup.example

3) Bellhaven Group of Companies, Rui Delcourt, Chief Operations Officer, 587-555-0163, ruidelcourt@bellhavengroup.example

Thank you so much for considering our project & we look forward to seeing your designs!

```html
<!DOCTYPE html>
<html lang="en">
<head>
<meta charset="utf-8">
<title>Bellhaven Group of Companies – Business Card</title>
<link href="https://fonts.googleapis.com/css2?family=Arimo:wght@400;500&family=Playfair+Display:wght@700&display=swap" rel="stylesheet">
<style>
  :root {
    --backdrop: #cfcfcf;
    --card-white: #ffffff;
    --card-black: #1e1e1e;
    --ink-black: #1a1a1a;
    --ink-white: #ffffff;
    --divider: rgba(255,255,255,0.55);
  }
  * { box-sizing: border-box; margin: 0; padding: 0; }
  html, body {
    width: 1200px; height: 788px; overflow: hidden;
    background: var(--backdrop);
  }
  .canvas {
    width: 1200px; height: 788px;
    display: flex; flex-direction: column; align-items: center; justify-content: center;
    gap: 40px;
  }
  .card {
    width: 600px; height: 343px;
    border-radius: 22px;
    position: relative; overflow: hidden;
    box-shadow: 0 6px 18px rgba(0,0,0,0.18);
  }

  /* Front */
  .card--front { background: var(--card-white); }
  .front__brand {
    position: absolute; left: 186px; top: 44px;
    display: flex; align-items: center; gap: 10px;
    font-family: "Arimo", sans-serif; font-weight: 500;
    color: var(--ink-black);
  }
  .brand__mark { width: 12px; height: 12px; background: var(--ink-black); }
  .brand__name { font-size: 20px; letter-spacing: 6px; line-height: 1.15; }
  .brand__name small { display: block; font-size: 10px; letter-spacing: 3px; }
  .front__band {
    position: absolute; left: 0; right: 0; top: 132px; height: 172px;
    background: var(--card-black);
    display: flex; align-items: center;
    padding: 0 30px 0 46px;
  }
  .person { width: 170px; color: var(--ink-white); }
  .person__name {
    font-family: "Playfair Display", serif; font-weight: 700;
    font-size: 21px; line-height: 1.2;
  }
  .person__title {
    font-family: "Arimo", sans-serif; font-size: 15px; margin-top: 2px;
  }
  .band__divider {
    width: 1px; height: 62px; background: var(--divider); margin: 0 22px 0 8px;
  }
  .contact { list-style: none; color: var(--ink-white); font-family: "Arimo", sans-serif; font-size: 15.5px; }
  .contact li { display: flex; align-items: center; gap: 8px; line-height: 1.75; }
  .contact svg { width: 13px; height: 13px; flex: none; }

  /* Back */
  .card--back {
    background: var(--card-black);
    display: flex; align-items: center; justify-content: center;
  }
  .back__brand {
    display: flex; align-items: center; gap: 16px;
    font-family: "Arimo", sans-serif; font-weight: 500; color: var(--ink-white);
  }
  .back__brand .brand__mark { width: 20px; height: 20px; background: var(--ink-white); }
  .back__brand .brand__name { font-size: 40px; letter-spacing: 12px; }
  .back__brand .brand__name small { font-size: 16px; letter-spacing: 6px; margin-top: 6px; }
</style>
</head>
<body>
<main class="canvas">
  <section class="card card--front" aria-label="Card front">
    <div class="front__brand">
      <span class="brand__mark"></span>
      <span class="brand__name">BELLHAVEN<small>GROUP OF COMPANIES</small></span>
    </div>
    <div class="front__band">
      <div class="person">
        <p class="person__name">Tobias Quenby</p>
        <p class="person__title">Chief Executive Officer</p>
      </div>
      <span class="band__divider"></span>
      <ul class="contact">
        <li>
          <svg viewBox="0 0 16 16" aria-hidden="true"><circle cx="8" cy="8" r="8" fill="#fff"/><path d="M5 4.5l1.6-.4.9 2-1 .8a6 6 0 0 0 2.6 2.6l.8-1 2 .9-.4 1.6c-3.5.3-6.8-3-6.5-6.5z" fill="#1e1e1e"/></svg>
          780-555-0187
        </li>
        <li>
          <svg viewBox="0 0 16 16" aria-hidden="true"><rect x="1" y="3.5" width="14" height="9" fill="#fff"/><path d="M1 3.5l7 5 7-5" fill="none" stroke="#1e1e1e" stroke-width="1.3"/></svg>
          tobiasquenby@bellhavengroup.example
        </li>
        <li>
          <svg viewBox="0 0 16 16" aria-hidden="true"><circle cx="8" cy="8" r="7.5" fill="#fff"/><path d="M.5 8h15M8 .5c-3 3.5-3 11.5 0 15M8 .5c3 3.5 3 11.5 0 15" fill="none" stroke="#1e1e1e" stroke-width="1"/></svg>
          www.bellhavengroup.example
        </li>
      </ul>
    </div>
  </section>

  <section class="card card--back" aria-label="Card back">
    <div class="back__brand">
      <span class="brand__mark"></span>
      <span class="brand__name">BELLHAVEN<small>GROUP OF COMPANIES</small></span>
    </div>
  </section>
</main>
</body>
</html>
```